Velmora Freightway Solutions Business cards

Would like a very unique design catchy but professional for business cards. Please use log provided.Marlon WellsCeo and Founder TransCon Logistix Solutions1-888-913-3225mwells@tlsolutionsus.comwww.tlsolutionsus.com

```html
<!DOCTYPE html>
<html lang="en">
<head>
<meta charset="utf-8">
<title>Velmora Freightway Solutions – Business Cards</title>
<link href="https://fonts.googleapis.com/css2?family=Lato:wght@400;700;900&display=swap" rel="stylesheet">
<style>
  :root {
    --backdrop: #161616;
    --card: #0e0e10;
    --card-edge: #1d1d20;
    --silver: #d9d9dc;
    --text-light: #d6d6d6;
    --blue: #1f7ac9;
    --red: #e3222c;
    --rule: #3a3a3e;
  }
  * { margin: 0; padding: 0; box-sizing: border-box; }
  html, body { width: 1200px; height: 900px; overflow: hidden; }
  body {
    background: var(--backdrop);
    font-family: "Lato", sans-serif;
    position: relative;
  }
  .card {
    position: absolute;
    left: 320px;
    width: 560px;
    height: 320px;
    border-radius: 22px;
    background: linear-gradient(135deg, var(--card-edge) 0%, var(--card) 55%);
    box-shadow: 0 18px 40px rgba(0,0,0,.6);
    overflow: hidden;
  }
  .card--front { top: 100px; }
  .card--back { top: 470px; }

  .front-brand {
    position: absolute;
    inset: 0;
    display: flex;
    align-items: center;
    justify-content: center;
    gap: 16px;
  }
  .brand-dot {
    width: 22px; height: 22px;
    border-radius: 50%;
    background: var(--silver);
  }
  .front-brand .brand-name {
    color: var(--silver);
    font-weight: 700;
    font-size: 30px;
    letter-spacing: 1px;
  }

  .back-brand {
    position: absolute;
    right: 34px;
    top: 44px;
    display: flex;
    align-items: center;
    gap: 10px;
  }
  .back-brand .brand-square {
    width: 14px; height: 14px;
    background: var(--blue);
  }
  .back-brand .brand-name {
    color: var(--blue);
    font-weight: 700;
    font-size: 19px;
    letter-spacing: .5px;
  }
  .rule {
    position: absolute;
    height: 1px;
    background: var(--rule);
  }
  .rule--top { right: 34px; top: 94px; width: 300px; }
  .rule--name { left: 220px; top: 172px; width: 306px; }

  .website {
    position: absolute;
    right: 34px;
    top: 108px;
    color: var(--blue);
    font-size: 15px;
  }
  .holder {
    position: absolute;
    left: 40px;
    top: 158px;
  }
  .holder-name {
    font-weight: 900;
    font-size: 22px;
    letter-spacing: 1px;
    text-transform: uppercase;
    color: var(--blue);
  }
  .holder-name .surname { color: var(--red); }
  .holder-role {
    color: var(--text-light);
    font-size: 15px;
    margin-top: 2px;
  }
  .contacts {
    position: absolute;
    left: 40px;
    top: 238px;
    list-style: none;
    color: var(--text-light);
    font-size: 15px;
  }
  .contacts li {
    display: flex;
    align-items: center;
    gap: 8px;
    margin-bottom: 6px;
  }
  .contacts svg { width: 14px; height: 14px; fill: var(--blue); }
</style>
</head>
<body>
  <section class="card card--front" aria-label="Card front">
    <div class="front-brand">
      <span class="brand-dot"></span>
      <span class="brand-name">Velmora Freightway Solutions</span>
    </div>
  </section>

  <section class="card card--back" aria-label="Card back">
    <div class="back-brand">
      <span class="brand-square"></span>
      <span class="brand-name">Velmora Freightway Solutions</span>
    </div>
    <div class="rule rule--top"></div>
    <div class="website">www.vfwayroutes.com</div>

    <div class="holder">
      <div class="holder-name">Dorian <span class="surname">Pike</span></div>
      <div class="holder-role">CEO and Founder</div>
    </div>
    <div class="rule rule--name"></div>

    <ul class="contacts">
      <li>
        <svg viewBox="0 0 16 16" aria-hidden="true"><path d="M3 1h3l1.5 4-2 1.3a9 9 0 0 0 4.2 4.2L11 8.5l4 1.5v3a2 2 0 0 1-2 2A12 12 0 0 1 1 3a2 2 0 0 1 2-2z"/></svg>
        1-888-470-6158
      </li>
      <li>
        <svg viewBox="0 0 16 16" aria-hidden="true"><path d="M1 3h14v10H1z M1 3l7 6 7-6" stroke="#0e0e10" stroke-width="1.2"/></svg>
        dpike@vfwayroutes.com
      </li>
    </ul>
  </section>
</body>
</html>
```